Business Card for a Dental Office

The design should communicate integrity, quality and reliability. We also want the card look elegant, simple, but still stand out, different from the traditional-dental-office business card.

Industry/Entity Type

Business

```html
<!DOCTYPE html>
<html lang="en">
<head>
<meta charset="utf-8">
<title>Harwell Dental Studio – Business Card</title>
<link rel="stylesheet" href="https://fonts.googleapis.com/css2?family=Oswald:wght@600&family=Open+Sans:wght@400;600&display=swap">
<style>
  :root {
    --ink: #0b0b0b;
    --paper: #ffffff;
    --gold: #d8b924;
    --gold-light: #f4e48a;
    --gold-deep: #b8961a;
    --muted: #d9d9d9;
    --stage: #e8e8e6;
  }
  * { margin: 0; padding: 0; box-sizing: border-box; }
  html, body { width: 1200px; height: 950px; overflow: hidden; }
  body { background: var(--stage); position: relative; font-family: "Open Sans", sans-serif; }

  .card { position: absolute; left: 250px; width: 700px; height: 400px; overflow: hidden; box-shadow: 0 10px 28px rgba(0,0,0,.18); }
  .card--front { top: 55px; background: var(--ink); }
  .card--back { top: 495px; background: var(--paper); }

  .brand { position: absolute; display: flex; align-items: center; gap: 14px; }
  .brand__mark { width: 46px; height: 46px; background: var(--gold); flex: none; }
  .brand__text { display: flex; flex-direction: column; }
  .brand__name { font-family: "Oswald", sans-serif; font-weight: 600; font-size: 34px; line-height: 1; letter-spacing: .5px; text-transform: uppercase; }
  .brand__tagline { font-family: "Open Sans", sans-serif; font-weight: 600; font-size: 13.5px; letter-spacing: 1.1px; color: var(--gold); text-transform: uppercase; margin-top: 4px; }

  .card--front .brand { left: 150px; top: 150px; }
  .card--front .brand__name { color: var(--paper); }
  .website { position: absolute; left: 0; right: 0; top: 300px; text-align: center; color: var(--muted); font-size: 15px; letter-spacing: 3px; }

  .card--back .brand { left: 120px; top: 70px; }
  .card--back .brand__name { color: var(--ink); }

  .gold-panel { position: absolute; left: 330px; top: 140px; width: 370px; height: 200px;
    background: linear-gradient(110deg, var(--gold-deep) 0%, var(--gold) 30%, var(--gold-light) 60%, var(--gold) 85%, var(--gold-deep) 100%); }
  .ink-band { position: absolute; left: 0; top: 220px; width: 330px; height: 120px; background: var(--ink); }

  .person { position: absolute; left: 28px; top: 232px; color: var(--paper); font-size: 15px; line-height: 1.45; }
  .person__name { color: var(--gold); font-size: 19px; font-weight: 600; }

  .contacts { position: absolute; right: 22px; top: 160px; list-style: none; text-align: right; color: #1a1a1a; font-size: 15px; line-height: 1.75; }
  .contacts li { display: flex; justify-content: flex-end; align-items: center; gap: 8px; }
  .contacts svg { width: 16px; height: 16px; fill: var(--ink); }
</style>
</head>
<body>

<section class="card card--front" aria-label="Card front">
  <div class="brand">
    <span class="brand__mark"></span>
    <div class="brand__text">
      <span class="brand__name">Harwell Dental Studio</span>
      <span class="brand__tagline">Your smile is your gift to others</span>
    </div>
  </div>
  <p class="website">www.harwelldental.com</p>
</section>

<section class="card card--back" aria-label="Card back">
  <div class="brand">
    <span class="brand__mark"></span>
    <div class="brand__text">
      <span class="brand__name">Harwell Dental Studio</span>
      <span class="brand__tagline">Your smile is your gift to others</span>
    </div>
  </div>

  <div class="gold-panel"></div>
  <div class="ink-band"></div>

  <div class="person">
    <p class="person__name">Mark Ellison</p>
    <p>President</p>
    <p>2140 Linden Avenue</p>
    <p>Cedar Falls, NY 10233</p>
  </div>

  <ul class="contacts">
    <li>555 0142 7781
      <svg viewBox="0 0 16 16" aria-hidden="true"><path d="M2 5c0-2 2-3 6-3s6 1 6 3v1h-3V4.5C10 4 6 4 5 4.5V6H2z"/><rect x="3" y="8" width="10" height="6" rx="1"/></svg></li>
    <li>555 0198 3364
      <svg viewBox="0 0 16 16" aria-hidden="true"><path d="M4 1h8v14H4z M5.5 2.5v9h5v-9z"/></svg></li>
    <li>555 0175 2409
      <svg viewBox="0 0 16 16" aria-hidden="true"><rect x="4" y="1" width="8" height="5"/><rect x="1" y="6" width="14" height="8" rx="1"/></svg></li>
    <li>mark@harwelldental.com
      <svg viewBox="0 0 16 16" aria-hidden="true"><path d="M1 3h14v10H1z"/><path d="M1 3l7 6 7-6" fill="none" stroke="#d8b924" stroke-width="1.4"/></svg></li>
  </ul>
</section>

</body>
</html>
```